PELLOS BAR AND RESTAURANT MENU, A SNOWBOARDING DRINKING HOLE IN THE MOUTAINS OF NEW ZEALAND

i would like a menu designed i have all the data in categories to copy and paste, i want A3 menu that has a black board feel with a splashes of bright color here and there with small pics scattered over it in drawing style like the attached, say a slice of pizza near the pizza menu a Mexican wrestler or mexican skull near the mexican, a drawing of a chicken a burger a slice of pizza ect 4 or 5 of drawing scattered , i want all the food on one side and drinks on the other side, i have attached the pellos logo ( i think i would look good in a shiny black on top of a mat black menu, maybe in the middle at the top?) this menu is targeting a young snowboard / skateboard crowd so i want it to be cool and fun! I have given a clear look and feel for the food side of the menu i would like to have the continuity on the drinks side but I look forward to your creativity on the other side of the menu for the drinks, please make the menu landscape all food on the front all drinks on the back

Target Market(s)

SNOWBOARDERS, YOUNG TRAVELERS, SKATEBOARDERS, COOL YOUTH

Industry/Entity Type

Hospitality

Requirements
Must have
• BLACKBOARD APPEARANCE WITH WHITE TEXT ( I DON'T MIND OLS TYPEWRITER FONT) SPLASHES OF BRIGHT COLORS WITH DRAWINGS OF SOME OF THE FOOD OPTIONS , A BURGER A SLICE OF PIZZA A CHICKEN A MEXICAN WRESTLER
Nice to have
• ANYTHING RELATED TO SNOWBOARDING AND MOUNTAINS AS WE ARE A BAR IN A SNOW TOWN IN QUEENSTOWN NEW ZEALAND

```html
<!DOCTYPE html>
<html lang="en">
<head>
<meta charset="utf-8">
<title>Pellos Bar and Restaurant – Menu</title>
<link href="https://fonts.googleapis.com/css2?family=Courier+Prime:wght@400;700&display=swap" rel="stylesheet">
<style>
:root{
  --page:#dcdcdc;
  --board-light:#3a3a3a;
  --board-dark:#0b0b0b;
  --chalk:#ffffff;
  --chalk-soft:#cfcfcf;
  --orange:#e08a1c;
  --splash-orange:#c47a16;
  --splash-red:#a8322c;
}
*{margin:0;padding:0;box-sizing:border-box}
html,body{width:1200px;height:1200px;overflow:hidden;background:var(--page)}
body{position:relative;font-family:"Courier Prime",monospace;color:var(--chalk)}
.sheet{position:absolute;overflow:hidden;
  background:radial-gradient(ellipse at 50% 35%,var(--board-light) 0%,#1c1c1c 55%,var(--board-dark) 100%);
  box-shadow:0 3px 8px rgba(0,0,0,.35)}
.sheet--food{left:262px;top:106px;width:689px;height:487px}
.sheet--drinks{left:263px;top:614px;width:686px;height:485px}
.frame{position:absolute;border:2px solid var(--chalk)}
.splash{position:absolute;border-radius:50%}
.splash--orange{background:radial-gradient(circle,var(--splash-orange) 55%,rgba(196,122,22,0) 72%)}
.splash--red{background:radial-gradient(circle,var(--splash-red) 55%,rgba(168,50,44,0) 72%)}
.sketch{position:absolute;background:radial-gradient(circle,rgba(255,255,255,.2),rgba(255,255,255,.04) 70%);border-radius:8px}
.sketch--warm{background:radial-gradient(circle,#f0a23a,#c47a16 80%);border-radius:6px}
.banner{position:absolute;z-index:2}
.banner svg{position:absolute;inset:0}
.banner span{position:absolute;inset:0;display:flex;align-items:center;justify-content:center;font-size:23px}
.brand{position:absolute;z-index:2;display:flex;align-items:center;justify-content:center;border-radius:50%;
  background:#d8d8d8;border:4px solid var(--orange);color:#222;font-weight:700;font-size:17px}
.col{position:absolute;z-index:2}
.h{font-weight:700;font-size:12.5px;line-height:1.1;margin-bottom:3px}
.h small{font-size:5.5px;color:var(--orange);font-weight:400;margin-left:6px;display:inline-block;line-height:1.2;vertical-align:top}
.intro{font-size:6px;line-height:1.2;margin-bottom:2px}
.item{display:flex;justify-content:space-between;font-size:5.6px;line-height:1.15;margin-top:4px}
.item b{font-weight:400;padding-right:4px}
.col--burger .item{font-size:5.2px}
.price{color:var(--orange);white-space:nowrap}
.desc{font-size:3.5px;line-height:1.25;color:var(--chalk-soft)}
.accent{color:var(--orange)}
.rule{position:absolute;width:2px;background:var(--chalk-soft)}
.pizza-row{display:flex;font-size:3.4px;line-height:1.25;margin-top:3px}
.pizza-row .name{width:30px;flex:none;color:var(--orange)}
.pizza-row .top{flex:1;color:var(--chalk-soft)}
.dlist{font-size:5.8px;line-height:13.6px}
.dh{font-weight:700;font-size:12.5px;line-height:1.2;margin-bottom:1px}
.dsub{font-weight:700;font-size:7.2px;line-height:1.25}
</style>
</head>
<body>

<!-- FOOD SIDE -->
<section class="sheet sheet--food" aria-label="Food menu">
  <div class="splash splash--orange" style="left:-8px;top:120px;width:58px;height:66px"></div>
  <div class="splash splash--orange" style="left:610px;top:-14px;width:90px;height:72px"></div>
  <div class="splash splash--red" style="left:640px;top:98px;width:70px;height:110px"></div>

  <div class="frame" style="left:40px;top:48px;width:602px;height:415px"></div>

  <div class="sketch sketch--warm" role="img" aria-label="Sketch of a pizza slice" style="left:0;top:0;width:88px;height:92px"></div>
  <div class="sketch" role="img" aria-label="Sketch of a skateboard" style="left:98px;top:74px;width:88px;height:36px"></div>
  <div class="sketch" role="img" aria-label="Sketches of luchador masks" style="left:214px;top:103px;width:44px;height:22px"></div>
  <div class="sketch" role="img" aria-label="Sketch of a young skater" style="left:442px;top:74px;width:48px;height:52px"></div>
  <div class="sketch" role="img" aria-label="Sketch of an acoustic guitar" style="left:574px;top:66px;width:56px;height:76px"></div>
  <div class="sketch" role="img" aria-label="Sketches of a chicken leg and vegetables" style="left:90px;top:148px;width:70px;height:40px"></div>
  <div class="sketch" role="img" aria-label="Sketches of a burger, skateboard and assorted food" style="left:0;top:250px;width:108px;height:237px"></div>
  <div class="sketch" role="img" aria-label="Sketch of a whole pizza" style="left:578px;top:392px;width:111px;height:95px;border-radius:50%"></div>
  <div class="sketch" role="img" aria-label="Small sketch of a sugar skull" style="left:492px;top:166px;width:24px;height:24px"></div>
  <div class="sketch" role="img" aria-label="Small sketch of a pizza slice" style="left:647px;top:226px;width:28px;height:28px"></div>

  <div class="brand" style="left:306px;top:14px;width:88px;height:88px">Pellos</div>

  <div class="banner" style="left:236px;top:130px;width:228px;height:40px">
    <svg viewBox="0 0 228 40" width="228" height="40"><polygon points="0,2 228,2 214,20 228,38 0,38 14,20" fill="none" stroke="#fff" stroke-width="2.5"/><polygon points="18,6 210,6 198,20 210,34 18,34 30,20" fill="var(--board-dark)" stroke="#fff" stroke-width="1.5"/></svg>
    <span>PIZZA MENU</span>
  </div>

  <div class="col col--burger" style="left:115px;top:194px;width:95px">
    <div class="h">BURGER</div>
    <div class="intro">All Burgers <span class="accent">$15</span> and are served with Chips</div>
    <div class="desc">Sweet dreams are made of cheese (cheeseburger)</div>
    <div class="item"><b>Beef Pattie, Lettuce, Tomato, Onion, Mayo &amp; Ketchup</b></div>
    <div class="desc">Pig Daddy (beef &amp; bacon)</div>
    <div class="item"><b>Beef Pattie, Bacon, BBQ Sauce</b></div>
    <div class="desc">Holy Cluck (chicken burger)</div>
    <div class="item"><b>Breaded Chicken, Lettuce Tomato &amp; Mayonnaise</b></div>
    <div class="desc">The Kiwi (fish burger)</div>
    <div class="item"><b>Battered Fish, Lettuce, Tomato, Tartare Sauce</b></div>
    <div class="desc">The Hipster Veg burger</div>
    <div class="item"><b>Veggie Pattie, Lettuce, Tomato, Onion, Mayo &amp; Ketchup</b></div>
    <div class="desc" style="margin-top:2px">Bacon, Pineapple, Egg, Cheese, Jalapeños</div>
    <div class="desc">Add On <span class="accent" style="font-size:6px">$2</span></div>
  </div>

  <div class="col" style="left:216px;top:194px;width:106px">
    <div class="h">STARTERS</div>
    <div class="item"><b>REMARKABLE SOUP WITH HOT CRUSTY ROLL</b><span class="price">$9.00</span></div>
    <div class="desc">ask staff for today's soup</div>
    <div class="item"><b>THE BOY FROM EMPANADA (CRAB AND CORN EMPANADAS)</b><span class="price">$9</span></div>
    <div class="desc">South American style crab and corn empanadas</div>
    <div class="item"><b>Wicked Wings</b><span class="price">$8</span></div>
    <div class="desc">Basket of wings with a sriracha mayo dipping sauce</div>
    <div class="item"><b>CHICK STRIPPERS (CHICKEN TENDERS)</b><span class="price">$8</span></div>
    <div class="desc">Served with a smokey BBQ dipping sauce</div>
    <div class="item"><b>SIDE SALAD</b><span class="price">$5</span></div>
    <div class="desc">Fresh garden side salad with your choice of Caesar or Italian dressing</div>
    <div class="item"><b>WEDGIE! KUMARA OR SWEET POTATO WEDGES</b><span class="price">$8.50</span></div>
    <div class="desc">Basket of wedges served with sour cream and sweet chilli</div>
    <div class="item"><b>SALT AND PEPPER SQUID</b><span class="price">$9</span></div>
    <div class="desc">Served with tartare sauce</div>
    <div class="item"><b>MARCO AND LACHEESY</b><span class="price">$8</span></div>
    <div class="desc">Cheesy garlic bread</div>
    <div class="item"><b>SAILOR'S SPINACH AND FETA ROLL</b><span class="price">$6.00</span></div>
    <div class="desc">Kai pai spinach and feta roll baked in a flaky pastry</div>
    <div class="item"><b>EYES ON THE FRIES</b><span class="price">$6.50</span></div>
    <div class="desc">Basket of french fries</div>
  </div>

  <div class="rule" style="left:338px;top:194px;height:252px"></div>

  <div class="col" style="left:360px;top:194px;width:106px">
    <div class="h">MAINS</div>
    <div class="item"><b>Caesar's castle</b><span class="price">$14</span></div>
    <div class="desc">Caesar salad <span class="accent">+ chicken $3</span></div>
    <div class="item"><b>Steak or Break</b><span class="price">$24</span></div>
    <div class="desc">Steak with chips, salad &amp; gravy</div>
    <div class="item"><b>Fush and Chups</b><span class="price">$16.50</span></div>
    <div class="desc">Battered fillet served with chips and tartare sauce</div>
    <div class="item"><b>Hasta la pasta baby</b><span class="price">$15</span></div>
    <div class="desc">ask staff for today's pasta selections</div>
    <div class="item"><b>What's your beef lasagne</b><span class="price">$15</span></div>
    <div class="desc">Traditional beef lasagne served with a side of salad</div>
    <div class="item"><b>Save the planet VEGAN and GF Lasagne</b><span class="price">$15</span></div>
    <div class="desc">Rainbow layers of country fresh vegetables in a GF lasagne with a side of salad</div>
    <div class="item"><b>Cardies Chicken Parmy</b><span class="price">$18.50</span></div>
    <div class="desc">Classic chicken parmy served with chips and salad</div>
    <div class="item"><b>Fritz's Schnitzel</b><span class="price">$18</span></div>
    <div class="desc">Chicken schnitzel and chips</div>
    <div class="item"><b>Im nacho Baby (nachos)</b><span class="price">$15</span></div>
    <div class="desc">Tortilla chips topped with cheese, chunky salsa, jalapeños, guacamole &amp; sour cream</div>
    <div class="desc accent">Add spicy beef <span style="font-size:5.6px">$3</span></div>
    <div class="item"><b>Lets taco bout it</b><span class="price">$15</span></div>
    <div class="desc">3 soft shell tacos with lettuce, tomato, cheese, salsa &amp; sour cream and <span class="accent">spicy beef, chicken or vegetables</span></div>
    <div class="item"><b>Quesadilla's from Mamacita</b><span class="price">$15</span></div>
    <div class="desc">Spicy beef or chicken quesadillas served with fries and guac &amp; sour cream dip</div>
  </div>

  <div class="col" style="left:492px;top:194px;width:140px">
    <div class="h">PIZZA</div>
    <div style="display:flex;justify-content:space-between;gap:6px">
      <div class="desc" style="width:100px;font-size:3.4px">All our Pizzas use Mozzarella cheese, freshly made Tomato sauce, seasoned with Italian Herbs and are served on a 13" base</div>
      <span class="price" style="font-size:5.6px;margin-right:36px">$16</span>
    </div>
    <div class="pizza-row"><span class="name">Garlic</span><span class="top">Garlic Butter Base, Cheese, Italian Herbs</span></div>
    <div class="pizza-row"><span class="name">Margherita</span><span class="top">Tomato Base, Sliced Tomato</span></div>
    <div class="pizza-row"><span class="name">Spicy Veg</span><span class="top">Tomato Base, Capsicum, Onion, Olive, Pineapple, Jalapeños, Chilli Flakes</span></div>
    <div class="pizza-row"><span class="name">Hawaiian</span><span class="top">Tomato Base, Ham, Pineapple</span></div>
    <div class="pizza-row"><span class="name">BBQ Chicken</span><span class="top">BBQ Base, Chicken, Bacon, Onion, topped with a BBQ drizzle</span></div>
    <div class="pizza-row"><span class="name">Pepperoni</span><span class="top">Tomato Base, Double Pepperoni, Double Cheese</span></div>
    <div class="pizza-row"><span class="name">Meat lovers</span><span class="top">Tomato or BBQ Base, Pepperoni, Bacon, Ham, Chilli Beef</span></div>
    <div class="pizza-row"><span class="name">Mexican</span><span class="top">Tomato Base, Chilli Beef, Onion, Capsicum, Jalapeños, Olives, Chilli Flakes (sour cream $2)</span></div>
    <div class="pizza-row"><span class="name">Supreme</span><span class="top">Pepperoni, bacon, capsicum, spicy beef, onion, mushroom, pineapple, olives, oregano</span></div>
  </div>

  <div class="col" style="left:492px;top:338px;width:130px">
    <div class="h">ICE CREAM<small>$5.50<br>for 2 Scoops</small></div>
    <div class="desc" style="width:118px">Finish your meal with a bowl of New Zealand's finest ice cream, available in four delicious flavours</div>
    <div class="desc" style="display:flex;gap:14px;margin-top:3px"><span>Vanilla<br>Hokey Pokey</span><span>Boysenberry<br>ripple</span></div>
    <div class="item" style="margin-top:8px;width:80px"><b>Loaded Fries &nbsp;All</b><span class="price">$9.50</span></div>
    <div class="desc">Alpine Poutine</div>
    <div class="desc" style="width:50px">Poutine-style fries smothered in cheese &amp; gravy</div>
    <div class="desc">The mad Mexican</div>
    <div class="desc" style="width:50px">Spicy Mexican ground beef covered fries topped with cheese</div>
    <div class="desc">Cheesy Bacon Bro</div>
    <div class="desc" style="width:50px">Fries topped with cheese and bacon goodness</div>
  </div>
</section>

<!-- DRINKS SIDE -->
<section class="sheet sheet--drinks" aria-label="Drinks menu">
  <div class="splash splash--orange" style="left:-14px;top:-14px;width:104px;height:84px"></div>
  <div class="splash splash--red" style="left:560px;top:345px;width:140px;height:140px"></div>

  <div class="frame" style="left:27px;top:28px;width:628px;height:429px"></div>

  <div class="sketch" role="img" aria-label="Sketch of a tree branch" style="left:626px;top:30px;width:26px;height:90px"></div>
  <div class="sketch" role="img" aria-label="Sketches of tall beer and cognac bottles" style="left:20px;top:355px;width:62px;height:128px"></div>
  <div class="sketch" role="img" aria-label="Sketches of cocktail glasses and bottles" style="left:88px;top:400px;width:210px;height:84px"></div>
  <div class="sketch" role="img" aria-label="Sketch of a skateboard" style="left:195px;top:346px;width:84px;height:50px"></div>
  <div class="sketch" role="img" aria-label="Sketch of a young skateboarder" style="left:350px;top:356px;width:96px;height:100px"></div>
  <div class="sketch" role="img" aria-label="Sketch of an acoustic guitar" style="left:505px;top:322px;width:70px;height:88px"></div>
  <div class="sketch" role="img" aria-label="Sketches of wine bottles and a citrus slice" style="left:594px;top:300px;width:90px;height:184px"></div>
  <div class="sketch" role="img" aria-label="Small sketches of beer mugs and bottles" style="left:56px;top:125px;width:28px;height:200px"></div>
  <div class="sketch" role="img" aria-label="Small sketch of a cocktail glass" style="left:282px;top:116px;width:20px;height:34px"></div>
  <div class="sketch" role="img" aria-label="Small sketch of a shot glass" style="left:282px;top:290px;width:20px;height:28px"></div>

  <div class="banner" style="left:250px;top:58px;width:218px;height:38px">
    <svg viewBox="0 0 218 38" width="218" height="38"><polygon points="0,2 218,2 204,19 218,36 0,36 14,19" fill="none" stroke="#fff" stroke-width="2.5"/><polygon points="18,6 200,6 189,19 200,32 18,32 29,19" fill="var(--board-dark)" stroke="#fff" stroke-width="1.5"/></svg>
    <span style="font-size:22px">DRINKS MENU</span>
  </div>

  <div class="col" style="left:91px;top:120px;width:104px">
    <div class="dh">DRAUGHT</div>
    <div class="dlist">Stoker's &nbsp;7<br>Orchard Row Apple Cider 8</div>
    <div class="dh" style="margin-top:3px">RTD'S</div>
    <div class="dlist" style="line-height:11px">Frostline Ice 7.5<br>Hot Cider:</div>
    <div class="dh" style="margin-top:3px">BOTTLED BEER</div>
    <div class="dlist" style="line-height:11px">Costa 7.5<br>Stoker's Mid Ale 7.5</div>
    <div class="dsub" style="margin-top:4px">WINE GLASS 6.5<br>BOTTLE 25</div>
    <div class="dsub" style="margin-top:4px;font-size:6px;display:flex;justify-content:space-between;width:96px">BUBBLES PICCOLO<span class="accent">$8</span></div>
    <div class="dsub" style="font-size:6px;margin-top:3px">WHITE</div>
    <div class="dlist" style="line-height:9.5px">Sauvignon Blanc<br>Chardonnay</div>
    <div class="dsub" style="font-size:6px;margin-top:4px">RED</div>
    <div class="dlist" style="line-height:10px">Merlot<br>Pinot Noir<br>Lindvale Piccolo of<br>sparkling wine <span class="accent">$8</span></div>
    <div class="dsub" style="font-size:5.5px;margin-top:1px">SPIRITS</div>
  </div>

  <div class="col" style="left:207px;top:120px;width:72px">
    <div class="dh">WHISKEY</div>
    <div class="dlist">Dunmore 7<br>Northern Lodge 8<br>Wild Kestrel Honey 8<br>Brookmills 9<br><span style="line-height:7px;display:inline-block">Johnny Rambler<br>Black 9</span></div>
    <div class="dh" style="margin-top:8px;line-height:1.25">VODKA, GIN<br>&amp; TEQUILA</div>
    <div class="dlist">Frostline &nbsp;7<br>Jose Alvarado 7<br>Grey Heron &nbsp;9<br>Gordale 7<br>Bayside Sapphire - 8<br>Mil Ocho 9</div>
  </div>

  <div class="col" style="left:313px;top:120px;width:92px">
    <div class="dh">RUM</div>
    <div class="dlist">Captain Mulgrave 7<br>Mulgrave Spice 8<br>Barbosa White Rum 8<br>Maliko 8<br>Deepwater 9</div>
    <div class="dh" style="margin-top:8px;line-height:1.25">BOURBON &amp;<br>BRANDY</div>
    <div class="dlist">McKinley 7<br>Wild Kestrel<br>Jack Dalton 8<br>Bellwether 9</div>
  </div>

  <div class="rule" style="left:411px;top:125px;height:210px"></div>

  <div class="col" style="left:441px;top:118px;width:96px">
    <div class="dh" style="line-height:1.15">TEA AND<br>COFEE $4</div>
    <div class="dlist">All teas<br>Flat White<br>Latte<br>Cappuccino<br>Tall black<br>Espresso<br>Hot chocolate<br>Soy milk add 50c</div>
    <div class="dh" style="margin-top:6px">LIQUORS</div>
    <div class="dlist">Bannons 8<br>Frangella 8<br>Corvelle &nbsp;8<br>Galvano 8<br>Kaluna 8</div>
  </div>

  <div class="col" style="left:547px;top:118px;width:90px">
    <div class="dh">JUICE 3,50</div>
    <div class="dlist">Cola<br>Cola Zero<br>Lemon Squash<br>Lemonade<br>Ginger ale<br>Red Ram<br>Soda water</div>
    <div class="dh" style="margin-top:6px">JUICE 3,50</div>
    <div class="dlist">Orange<br>Pineapple<br>Apple<br>Cranberry</div>
  </div>
</section>

</body>
</html>
```